Bright, Bold Sydney Tutoring Business Flyer Advertisment

Lumora is an up and coming tutoring business located on Sydney's Upper North Shore catering to school students of all ages. We need a flyer designed for notice boards and letter box drops to attract new clients. Our tutors are mostly university education students who are fresh, dedicated and passionate about their areas of teaching. The flyer should exhibit a bright, bold, modern, clean cut style which would appeal to both students and parents. I have attached our logo (the flyer could reflect this colour scheme), and a PDF which outlines the information we would like to appear on the flyer. This is not set in stone, but designed to act as an extremely loose guide for your creativity !

Target Market(s)

Affluent School Students and Parents

Industry/Entity Type

Tutoring

Requirements
Must have
• Logo, $10 offer, company description.
Nice to have
• Grabbing headlines to attract new clients, such as "Feeling overwhelmed at school?". We are looking for an eye catching, clean cut and professional design that has the colours to attract kids and the tone to attract parents.

```html
<!DOCTYPE html>
<html lang="en">
<head>
<meta charset="utf-8">
<title>Lumora Tutoring Flyer</title>
<link href="https://fonts.googleapis.com/css2?family=Roboto+Slab:wght@600&family=Questrial&display=swap" rel="stylesheet">
<style>
  :root {
    --page-bg: #e9e8ec;
    --paper: #ffffff;
    --ink: #3b3b3d;
    --brand-blue: #4a9dd8;
    --brand-pink: #ea7fa3;
    --footer-bg: #050505;
    --headline: #ffffff;
    --photo-deep: #2e5d86;
    --photo-mid: #6f96b8;
    --photo-warm: #c9925e;
  }
  * { margin: 0; padding: 0; box-sizing: border-box; }
  html, body { width: 969px; height: 1200px; overflow: hidden; }
  body { background: var(--page-bg); position: relative; font-family: "Questrial", sans-serif; }

  .flyer {
    position: absolute; left: 95px; top: 58px;
    width: 779px; height: 1083px;
    background: var(--paper);
    box-shadow: 0 6px 20px rgba(0,0,0,0.18);
    overflow: hidden;
  }

  .hero-photo {
    position: absolute; left: 0; top: 0; width: 779px; height: 516px;
    background:
      linear-gradient(90deg, rgba(20,40,70,0.55) 0%, rgba(20,40,70,0.25) 55%, rgba(20,40,70,0) 75%),
      radial-gradient(ellipse at 75% 45%, #7f9fc4 0%, rgba(127,159,196,0) 45%),
      linear-gradient(160deg, var(--photo-deep) 0%, var(--photo-mid) 35%, var(--photo-warm) 60%, var(--photo-mid) 80%, var(--photo-deep) 100%);
  }

  .headlines { position: absolute; left: 47px; top: 110px; }
  .headline {
    position: absolute; left: 0; width: 420px;
    border-left: 3px solid var(--brand-pink);
    padding-left: 11px;
    font-family: "Roboto Slab", serif; font-weight: 600;
    font-size: 24px; line-height: 29px; letter-spacing: 0.5px;
    text-transform: uppercase; color: var(--headline);
    white-space: nowrap;
  }
  .headline--one { top: 0; }
  .headline--two { top: 76px; }
  .headline--three { top: 188px; }

  .description {
    position: absolute; left: 60px; top: 540px; width: 661px;
    font-size: 20px; line-height: 26px; color: var(--ink);
    letter-spacing: -0.2px;
    text-align: justify; text-align-last: left;
  }

  .offer {
    position: absolute; left: 61px; top: 658px; width: 649px; height: 82px;
    background: var(--brand-blue); color: #fff;
    display: flex; flex-direction: column; justify-content: center; align-items: center;
    font-size: 29px; line-height: 34px; text-transform: uppercase; letter-spacing: -0.3px;
    white-space: nowrap;
  }

  .call-to-action {
    position: absolute; left: 0; top: 752px; width: 779px;
    text-align: center; font-size: 13px; color: var(--ink); text-transform: uppercase;
    white-space: nowrap;
  }

  .brand {
    position: absolute; left: 0; top: 890px; width: 779px;
    display: flex; justify-content: center; align-items: center; gap: 16px;
  }
  .brand-dot { width: 40px; height: 40px; border-radius: 50%; background: var(--brand-blue); }
  .brand-name { font-size: 60px; line-height: 1; color: var(--ink); text-transform: lowercase; }

  .footer {
    position: absolute; left: 0; top: 1005px; width: 779px; height: 78px;
    background: var(--footer-bg); color: #fff;
  }
  .footer-row { position: absolute; left: 0; width: 100%; display: flex; justify-content: center; gap: 24px; white-space: nowrap; }
  .footer-row--web { top: 10px; font-size: 19px; }
  .footer-row--address { top: 44px; font-size: 15px; }
  .contact-item { display: flex; align-items: center; gap: 9px; }
  .contact-item svg { display: block; }
</style>
</head>
<body>
  <main class="flyer">
    <div class="hero-photo" role="img" aria-label="Photo of a smiling teenage student holding a geography book in front of a world map"></div>

    <div class="headlines">
      <p class="headline headline--one">Feeling overwhelmed<br>by the HSC?</p>
      <p class="headline headline--two">Looking to improve<br>your skills,confidence<br>and organisation?</p>
      <p class="headline headline--three">Want to increase your<br>child’s engagement<br>at school?</p>
    </div>

    <p class="description">Lumora Tutoring offers one-on-one, individualised learning experiences to maximise academic development. Our tutors are hand selected on the basis of their qualifications, expertise and passion for inspiring young learners.</p>

    <div class="offer">
      <span>Mention this advertisement to claim</span>
      <span>your trial session for just $10!</span>
    </div>

    <p class="call-to-action">Contact us today to discuss how we can help make your learning goals a reality!</p>

    <div class="brand">
      <span class="brand-dot"></span>
      <span class="brand-name">lumora</span>
    </div>

    <footer class="footer">
      <div class="footer-row footer-row--web">
        <span class="contact-item">
          <svg width="18" height="14" viewBox="0 0 18 14" aria-hidden="true"><rect x="0" y="0" width="18" height="14" rx="2" fill="var(--brand-pink)"/><rect x="3" y="5" width="12" height="3" fill="var(--footer-bg)"/></svg>
          info@lumoratutoring.com.au
        </span>
        <span class="contact-item">
          <svg width="17" height="17" viewBox="0 0 17 17" aria-hidden="true"><rect width="17" height="17" rx="3" fill="var(--brand-pink)"/><circle cx="8.5" cy="8.5" r="4.5" fill="none" stroke="var(--footer-bg)" stroke-width="1.6"/><line x1="4" y1="8.5" x2="13" y2="8.5" stroke="var(--footer-bg)" stroke-width="1.2"/></svg>
          www/lumoratutoring.com.au
        </span>
      </div>
      <div class="footer-row footer-row--address">
        <span class="contact-item">
          <svg width="14" height="15" viewBox="0 0 14 15" aria-hidden="true"><rect width="14" height="15" rx="2" fill="var(--brand-pink)"/><path d="M7 3a3 3 0 0 1 3 3c0 2.2-3 5.5-3 5.5S4 8.2 4 6a3 3 0 0 1 3-3z" fill="var(--footer-bg)"/><circle cx="7" cy="6" r="1" fill="var(--brand-pink)"/></svg>
          Suite 4, 220 Harbour Road Linfield, Nsw 2070
        </span>
      </div>
    </footer>
  </main>
</body>
</html>
```